FinTech company looking to revamp and expand client-facing interface for our financial models

Pellworth Engines currently has a very simple website that allows clients to interact with our financial models. We are looking to completely redesign the current site and add several extra pages to provide extra functionality. We want the design to have a modern, slick feel, that will work on both a desktop or a tablet. It should be straightforward for clients to move between different pages at any time, and clear from the layout how to interact with the more advanced features. We have included screenshots of existing pages in the attached design brief, as well as sketches of the functionality required by the new pages, but can't provide a direct link to the current site.
Target Market(s)
Professional investors that will be paying to access the interface
Industry/Entity Type
Finance
Number of Pages Required
4 page
Colors
Designer to choose colors to be used in the design.
Look and feel
Each slider illustrates characteristics of the customer's brand and the style your logo design should communicate.

```html
<!DOCTYPE html>
<html lang="en">
<head>
<meta charset="utf-8">
<title>Pellworth Engines · Backtest</title>
<link rel="stylesheet" href="https://fonts.googleapis.com/css2?family=Montserrat:wght@500;600;700&family=Open+Sans:wght@400;600;700&display=swap">
<style>
:root{
  --navy:#0d2d5a;
  --teal:#0b6b63;
  --ink:#1a1a1a;
  --text:#222;
  --muted:#666;
  --band:#ececec;
  --page:#f7f7f7;
  --line:#e2e2e2;
  --row-alt:#f2f2f2;
  --blue:#3d6fb0;
  --olive:#b8b83a;
  --green:#3c9a3c;
}
*{box-sizing:border-box;margin:0;padding:0}
html,body{width:1200px;height:1094px;overflow:hidden;background:var(--page)}
.stage{position:absolute;left:0;top:0;width:1300px;height:1185px;transform:scale(.9231);transform-origin:0 0;font-family:"Open Sans",sans-serif;color:var(--text);
  background:linear-gradient(#e6e6e6 60px,#ededed 300px,#f2f2f2 610px,var(--page) 615px)}
.topbar{position:absolute;left:0;top:0;width:1300px;height:60px;background:#fff;box-shadow:0 2px 6px rgba(0,0,0,.08)}
.brand{position:absolute;left:72px;top:0;line-height:60px;font-weight:700;font-size:19px;color:var(--ink)}
.horizon{position:absolute;top:0;height:60px;line-height:60px;text-align:center;font-weight:700;font-size:15px;border-left:1px solid var(--line)}
.nav{position:absolute;top:0;height:60px;display:flex;align-items:center;justify-content:center;gap:9px;font-weight:700;font-size:14px;border-left:1px solid var(--line);color:var(--ink)}
.nav.active{background:var(--navy);color:#fff}
.options{position:absolute;left:0;top:315px;width:50px;height:250px;background:#d9d9d9;border-radius:0 4px 4px 0}
.options span{position:absolute;left:8px;top:482px;transform-origin:0 0;transform:rotate(-90deg);font-family:Montserrat,sans-serif;font-weight:600;font-size:17px;letter-spacing:1px;color:var(--ink);position:fixed}
.options-label{position:absolute;left:10px;top:170px;transform:rotate(-90deg);transform-origin:0 0;font-family:Montserrat,sans-serif;font-weight:600;font-size:17px;letter-spacing:1px;color:var(--ink)}
.options-toggle{position:absolute;left:36px;top:426px}
.chart-card{position:absolute;left:105px;top:100px;width:1160px;height:425px;background:#fff;border-radius:3px;box-shadow:0 1px 6px rgba(0,0,0,.1);overflow:hidden}
.chart-card .band{position:absolute;left:0;top:0;width:100%;height:85px;background:#eee}
.tab{position:absolute;top:50px;height:35px;line-height:35px;text-align:center;font-family:Montserrat,sans-serif;font-weight:500;font-size:17px;background:#fff;color:var(--ink);border-radius:3px 3px 0 0}
.tab.primary{background:var(--teal);color:#fff;font-weight:600}
.tab.hover{top:40px;height:45px;line-height:45px;background:#c8c8c8;color:#555}
.chart{position:absolute;left:0;top:0}
.export{position:absolute;top:577px;display:flex;align-items:center;gap:8px;font-family:Montserrat,sans-serif;font-weight:600;font-size:17px;color:var(--navy)}
.table{position:absolute;top:615px;height:490px;background:#fff;box-shadow:0 1px 6px rgba(0,0,0,.12);overflow:hidden}
.table .head{display:flex;height:70px;background:var(--ink);color:#fff;font-family:Montserrat,sans-serif;font-weight:600;font-size:17px}
.table .head div{display:flex;align-items:center;justify-content:center;border-right:1px solid #444}
.table .head div:last-child{border-right:0}
.table .row{display:flex;height:70px;font-size:17px}
.table .row:nth-child(odd){background:var(--row-alt)}
.table .row div{display:flex;align-items:center;justify-content:center;border-right:1px solid #ececec}
.scroll{position:absolute;top:95px;width:18px;height:370px;border:1px solid #ccc;border-radius:9px;background:#fff}
.scroll i{position:absolute;left:0;top:0;width:16px;height:74px;border-radius:8px;background:#999}
.gutter{position:absolute;top:70px;width:40px;height:420px;background:#f0f0f0}
</style>
</head>
<body>
<div class="stage">
  <header class="topbar">
    <div class="brand">KVANTA</div>
    <div class="horizon" style="left:196px;width:90px">250D</div>
    <div class="horizon" style="left:286px;width:90px">83D</div>
    <div class="horizon" style="left:376px;width:90px;border-right:1px solid var(--line)">42D</div>
    <div class="nav" style="left:601px;width:140px">
      <svg width="24" height="22" viewBox="0 0 24 22"><path d="M12 2 1 11h3v10h6v-6h4v6h6V11h3z" fill="#111"/></svg>MODELS</div>
    <div class="nav" style="left:741px;width:177px">
      <svg width="24" height="24" viewBox="0 0 24 24" fill="#111"><circle cx="12" cy="12" r="3"/><g><circle cx="12" cy="3" r="1.6"/><circle cx="12" cy="21" r="1.6"/><circle cx="3" cy="12" r="1.6"/><circle cx="21" cy="12" r="1.6"/><circle cx="5.6" cy="5.6" r="1.6"/><circle cx="18.4" cy="18.4" r="1.6"/><circle cx="18.4" cy="5.6" r="1.6"/><circle cx="5.6" cy="18.4" r="1.6"/><circle cx="12" cy="7.5" r="1.2"/><circle cx="12" cy="16.5" r="1.2"/><circle cx="7.5" cy="12" r="1.2"/><circle cx="16.5" cy="12" r="1.2"/></g></svg>SENSITIVITIES</div>
    <div class="nav" style="left:918px;width:160px">
      <svg width="24" height="24" viewBox="0 0 24 24" fill="none" stroke="#111" stroke-width="2"><circle cx="6" cy="6" r="4"/><circle cx="18" cy="6" r="4"/><circle cx="6" cy="18" r="4"/><circle cx="18" cy="18" r="4"/></svg>PORTFOLIO</div>
    <div class="nav active" style="left:1078px;width:152px">
      <svg width="24" height="20" viewBox="0 0 24 20" fill="none" stroke="#fff" stroke-width="2"><rect x="1" y="1" width="22" height="18"/><path d="M4 15l5-6 4 4 6-8"/></svg>BACKTEST</div>
  </header>

  <aside class="options">
    <div class="options-label">OPTIONS</div>
  </aside>
  <svg class="options-toggle" width="30" height="30" viewBox="0 0 30 30" style="position:absolute"><circle cx="15" cy="15" r="13" fill="var(--navy)" stroke="#fff" stroke-width="2"/><path d="M8 15h13M16 10l5 5-5 5" stroke="#fff" stroke-width="2.4" fill="none"/></svg>

  <section class="chart-card">
    <div class="band"></div>
    <div class="tab primary" style="left:55px;width:155px">Chart</div>
    <div class="tab" style="left:215px;width:90px">#1</div>
    <div class="tab" style="left:310px;width:90px">#2</div>
    <div class="tab" style="left:405px;width:90px">#3</div>
    <div class="tab hover" style="left:500px;width:90px">#4</div>
    <svg class="chart" width="1160" height="425" viewBox="105 100 1160 425" font-family="Open Sans,sans-serif" font-size="11" fill="#555">
      <g stroke="#eee">
        <line x1="190" y1="248" x2="1110" y2="248"/><line x1="190" y1="285" x2="1110" y2="285"/>
        <line x1="190" y1="322" x2="1110" y2="322"/><line x1="190" y1="360" x2="1110" y2="360"/>
        <line x1="190" y1="397" x2="1110" y2="397"/>
        <line x1="217" y1="240" x2="217" y2="434"/><line x1="359" y1="240" x2="359" y2="434"/>
        <line x1="500" y1="240" x2="500" y2="434"/><line x1="640" y1="240" x2="640" y2="434"/>
        <line x1="777" y1="240" x2="777" y2="434"/><line x1="917" y1="240" x2="917" y2="434"/>
        <line x1="1057" y1="240" x2="1057" y2="434"/>
      </g>
      <line x1="184" y1="434.5" x2="1112" y2="434.5" stroke="#777"/>
      <g text-anchor="end"><text x="186" y="252">100</text><text x="186" y="289">80</text><text x="186" y="326">60</text><text x="186" y="364">40</text><text x="186" y="401">20</text><text x="186" y="438">0</text></g>
      <g text-anchor="middle"><text x="217" y="461">Jul 2018</text><text x="359" y="461">Sep 2018</text><text x="500" y="461">Nov 2018</text><text x="640" y="461">Jan 2019</text><text x="777" y="461">Mar 2019</text><text x="917" y="461">May 2019</text><text x="1057" y="461">Jul 2019</text></g>

      <g stroke-width="7" stroke-linecap="round" stroke-dasharray="0 6">
        <line x1="236" y1="248" x2="320" y2="248" stroke="var(--olive)"/>
        <line x1="575" y1="249" x2="612" y2="249" stroke="var(--olive)"/>
        <line x1="790" y1="251" x2="1050" y2="251" stroke="var(--olive)"/>
        <line x1="625" y1="248" x2="1062" y2="248" stroke="var(--blue)" stroke-dasharray="0 7"/>
      </g>

      <g fill="var(--olive)">
        <circle cx="322" cy="263" r="3.5"/><circle cx="326" cy="257" r="3.5"/><circle cx="330" cy="265" r="3.5"/><circle cx="335" cy="254" r="3.5"/><circle cx="340" cy="252" r="3.5"/><circle cx="345" cy="255" r="3.5"/><circle cx="350" cy="254" r="3.5"/><circle cx="355" cy="255" r="3.5"/><circle cx="365" cy="259" r="3.5"/><circle cx="369" cy="261" r="3.5"/>
        <circle cx="372" cy="313" r="3.5"/><circle cx="376" cy="354" r="3.5"/><circle cx="384" cy="324" r="3.5"/><circle cx="387" cy="330" r="3.5"/><circle cx="390" cy="347" r="3.5"/><circle cx="394" cy="356" r="3.5"/><circle cx="398" cy="350" r="3.5"/><circle cx="402" cy="345" r="3.5"/><circle cx="406" cy="348" r="3.5"/><circle cx="410" cy="341" r="3.5"/><circle cx="414" cy="319" r="3.5"/><circle cx="418" cy="308" r="3.5"/><circle cx="422" cy="289" r="3.5"/><circle cx="426" cy="285" r="3.5"/><circle cx="430" cy="274" r="3.5"/><circle cx="434" cy="248" r="3.5"/><circle cx="438" cy="255" r="3.5"/><circle cx="442" cy="252" r="3.5"/><circle cx="446" cy="308" r="3.5"/><circle cx="450" cy="317" r="3.5"/><circle cx="454" cy="332" r="3.5"/><circle cx="458" cy="335" r="3.5"/><circle cx="462" cy="330" r="3.5"/>
        <circle cx="464" cy="395" r="3.5"/><circle cx="468" cy="378" r="3.5"/><circle cx="472" cy="399" r="3.5"/><circle cx="476" cy="393" r="3.5"/><circle cx="480" cy="401" r="3.5"/><circle cx="484" cy="384" r="3.5"/><circle cx="488" cy="419" r="3.5"/><circle cx="492" cy="415" r="3.5"/><circle cx="496" cy="419" r="3.5"/><circle cx="500" cy="412" r="3.5"/><circle cx="504" cy="430" r="3.5"/><circle cx="508" cy="427" r="3.5"/><circle cx="512" cy="423" r="3.5"/><circle cx="516" cy="425" r="3.5"/><circle cx="520" cy="408" r="3.5"/><circle cx="525" cy="414" r="3.5"/><circle cx="530" cy="408" r="3.5"/><circle cx="535" cy="397" r="3.5"/><circle cx="542" cy="386" r="3.5"/><circle cx="546" cy="378" r="3.5"/><circle cx="552" cy="380" r="3.5"/><circle cx="558" cy="373" r="3.5"/><circle cx="562" cy="332" r="3.5"/><circle cx="566" cy="328" r="3.5"/><circle cx="570" cy="324" r="3.5"/><circle cx="573" cy="321" r="3.5"/>
        <circle cx="612" cy="423" r="3.5"/><circle cx="618" cy="425" r="3.5"/><circle cx="624" cy="419" r="3.5"/><circle cx="630" cy="423" r="3.5"/><circle cx="636" cy="412" r="3.5"/><circle cx="642" cy="415" r="3.5"/><circle cx="648" cy="408" r="3.5"/><circle cx="654" cy="412" r="3.5"/><circle cx="660" cy="410" r="3.5"/><circle cx="666" cy="415" r="3.5"/><circle cx="672" cy="419" r="3.5"/><circle cx="676" cy="410" r="3.5"/><circle cx="680" cy="397" r="3.5"/><circle cx="684" cy="388" r="3.5"/><circle cx="688" cy="382" r="3.5"/><circle cx="690" cy="311" r="3.5"/><circle cx="694" cy="361" r="3.5"/><circle cx="696" cy="352" r="3.5"/><circle cx="704" cy="311" r="3.5"/><circle cx="706" cy="270" r="3.5"/><circle cx="710" cy="268" r="3.5"/><circle cx="722" cy="270" r="3.5"/><circle cx="726" cy="322" r="3.5"/><circle cx="738" cy="270" r="3.5"/><circle cx="742" cy="261" r="3.5"/><circle cx="746" cy="304" r="3.5"/><circle cx="750" cy="313" r="3.5"/><circle cx="752" cy="294" r="3.5"/><circle cx="756" cy="348" r="3.5"/><circle cx="758" cy="259" r="3.5"/><circle cx="762" cy="257" r="3.5"/><circle cx="768" cy="261" r="3.5"/><circle cx="772" cy="268" r="3.5"/><circle cx="776" cy="270" r="3.5"/><circle cx="782" cy="254" r="3.5"/><circle cx="786" cy="261" r="3.5"/><circle cx="790" cy="265" r="3.5"/>
      </g>
      <g fill="var(--blue)">
        <circle cx="238" cy="313" r="3.5"/><circle cx="241" cy="257" r="3.5"/><circle cx="244" cy="252" r="3.5"/><circle cx="250" cy="254" r="3.5"/><circle cx="255" cy="257" r="3.5"/><circle cx="259" cy="328" r="3.5"/><circle cx="262" cy="360" r="3.5"/><circle cx="266" cy="356" r="3.5"/><circle cx="270" cy="373" r="3.5"/><circle cx="273" cy="378" r="3.5"/><circle cx="275" cy="389" r="3.5"/><circle cx="278" cy="378" r="3.5"/><circle cx="282" cy="365" r="3.5"/><circle cx="286" cy="382" r="3.5"/><circle cx="288" cy="363" r="3.5"/><circle cx="290" cy="324" r="3.5"/><circle cx="294" cy="350" r="3.5"/><circle cx="297" cy="348" r="3.5"/><circle cx="300" cy="350" r="3.5"/><circle cx="304" cy="326" r="3.5"/><circle cx="307" cy="356" r="3.5"/><circle cx="310" cy="389" r="3.5"/><circle cx="315" cy="386" r="3.5"/><circle cx="318" cy="378" r="3.5"/><circle cx="320" cy="348" r="3.5"/><circle cx="324" cy="363" r="3.5"/><circle cx="328" cy="356" r="3.5"/><circle cx="333" cy="389" r="3.5"/><circle cx="337" cy="378" r="3.5"/><circle cx="340" cy="382" r="3.5"/><circle cx="344" cy="389" r="3.5"/><circle cx="348" cy="380" r="3.5"/><circle cx="352" cy="382" r="3.5"/><circle cx="356" cy="389" r="3.5"/><circle cx="368" cy="395" r="3.5"/><circle cx="372" cy="412" r="3.5"/><circle cx="377" cy="414" r="3.5"/><circle cx="382" cy="406" r="3.5"/><circle cx="386" cy="401" r="3.5"/><circle cx="390" cy="408" r="3.5"/><circle cx="395" cy="410" r="3.5"/><circle cx="398" cy="406" r="3.5"/><circle cx="402" cy="404" r="3.5"/><circle cx="406" cy="402" r="3.5"/><circle cx="412" cy="412" r="3.5"/><circle cx="418" cy="382" r="3.5"/><circle cx="422" cy="393" r="3.5"/><circle cx="426" cy="378" r="3.5"/><circle cx="430" cy="376" r="3.5"/><circle cx="434" cy="397" r="3.5"/><circle cx="438" cy="401" r="3.5"/><circle cx="442" cy="397" r="3.5"/><circle cx="446" cy="386" r="3.5"/><circle cx="450" cy="378" r="3.5"/><circle cx="454" cy="393" r="3.5"/><circle cx="458" cy="399" r="3.5"/><circle cx="462" cy="389" r="3.5"/><circle cx="466" cy="432" r="3.5"/><circle cx="470" cy="404" r="3.5"/><circle cx="476" cy="401" r="3.5"/><circle cx="480" cy="428" r="3.5"/><circle cx="484" cy="414" r="3.5"/><circle cx="488" cy="397" r="3.5"/><circle cx="492" cy="404" r="3.5"/><circle cx="496" cy="376" r="3.5"/><circle cx="498" cy="304" r="3.5"/><circle cx="502" cy="276" r="3.5"/><circle cx="508" cy="280" r="3.5"/><circle cx="512" cy="259" r="3.5"/><circle cx="515" cy="270" r="3.5"/><circle cx="520" cy="287" r="3.5"/><circle cx="524" cy="283" r="3.5"/><circle cx="528" cy="412" r="3.5"/><circle cx="533" cy="402" r="3.5"/><circle cx="538" cy="410" r="3.5"/><circle cx="540" cy="397" r="3.5"/><circle cx="545" cy="386" r="3.5"/><circle cx="550" cy="386" r="3.5"/><circle cx="556" cy="384" r="3.5"/><circle cx="560" cy="399" r="3.5"/><circle cx="564" cy="365" r="3.5"/><circle cx="567" cy="358" r="3.5"/><circle cx="570" cy="354" r="3.5"/><circle cx="575" cy="352" r="3.5"/><circle cx="578" cy="268" r="3.5"/><circle cx="580" cy="261" r="3.5"/><circle cx="585" cy="255" r="3.5"/><circle cx="590" cy="254" r="3.5"/><circle cx="596" cy="257" r="3.5"/><circle cx="600" cy="261" r="3.5"/><circle cx="605" cy="267" r="3.5"/><circle cx="610" cy="259" r="3.5"/>
        <circle cx="727" cy="391" r="3.5"/><circle cx="734" cy="391" r="3.5"/><circle cx="738" cy="401" r="3.5"/>
      </g>
      <g fill="var(--green)"><circle cx="1035" cy="432" r="3.5"/><circle cx="1040" cy="432" r="3.5"/><circle cx="1045" cy="432" r="3.5"/></g>

      <text x="1167" y="250" font-family="serif" font-size="11" fill="#444">Names</text>
      <g>
        <circle cx="1150" cy="246" r="3.5" fill="#8fb8de"/><circle cx="1150" cy="265" r="3.5" fill="#f4b27a"/><circle cx="1150" cy="284" r="3.5" fill="var(--green)"/><circle cx="1150" cy="302" r="3.5" fill="#e07a8a"/><circle cx="1150" cy="321" r="3.5" fill="#c49bd8"/><circle cx="1150" cy="340" r="3.5" fill="#b09a90"/><circle cx="1150" cy="358" r="3.5" fill="#f2a8d4"/><circle cx="1150" cy="377" r="3.5" fill="#bdbdbd"/><circle cx="1150" cy="396" r="3.5" fill="var(--olive)"/><circle cx="1150" cy="414" r="3.5" fill="#8fdbe0"/><circle cx="1150" cy="433" r="3.5" fill="var(--blue)"/>
      </g>
    </svg>
  </section>

  <div class="export" style="left:414px">
    <svg width="26" height="24" viewBox="0 0 26 24" fill="none" stroke="var(--navy)" stroke-width="2.2"><path d="M11 5H3v17h17v-7"/><path d="M9 16c1-6 5-9 12-9M17 3l5 4-5 4"/></svg>Export</div>
  <div class="export" style="left:1174px">
    <svg width="26" height="24" viewBox="0 0 26 24" fill="none" stroke="var(--navy)" stroke-width="2.2"><path d="M11 5H3v17h17v-7"/><path d="M9 16c1-6 5-9 12-9M17 3l5 4-5 4"/></svg>Export</div>

  <section class="table" style="left:105px;width:400px">
    <div class="head"><div style="width:360px">Stats</div></div>
    <div class="rows">
      <div class="row"><div style="width:180px">Stat 1</div><div style="width:180px">0.5</div></div>
      <div class="row"><div style="width:180px">Stat 2</div><div style="width:180px">-3</div></div>
      <div class="row"><div style="width:180px">Stat 3</div><div style="width:180px">30%</div></div>
      <div class="row"><div style="width:180px">Stat 4</div><div style="width:180px">0.5</div></div>
      <div class="row"><div style="width:180px">Stat 5</div><div style="width:180px">-3</div></div>
      <div class="row"><div style="width:180px">Stat 6</div><div style="width:180px">30%</div></div>
    </div>
    <div class="gutter" style="left:360px"></div>
    <div class="scroll" style="left:371px"><i></i></div>
  </section>

  <section class="table" style="left:545px;width:720px">
    <div class="head"><div style="width:180px">Open</div><div style="width:180px">Close</div><div style="width:180px">Size</div><div style="width:180px">Return</div></div>
    <div class="rows">
      <div class="row"><div style="width:180px">2018-04-05</div><div style="width:180px">2018-04-07</div><div style="width:180px">13</div><div style="width:180px">5%</div></div>
      <div class="row"><div style="width:180px">2018-04-05</div><div style="width:180px">2018-04-07</div><div style="width:180px">12</div><div style="width:180px">7%</div></div>
      <div class="row"><div style="width:180px">2018-04-05</div><div style="width:180px">2018-04-07</div><div style="width:180px">15</div><div style="width:180px">6%</div></div>
      <div class="row"><div style="width:180px">2018-04-05</div><div style="width:180px">2018-04-07</div><div style="width:180px">16</div><div style="width:180px">9%</div></div>
      <div class="row"><div style="width:180px">2018-04-05</div><div style="width:180px">2018-04-07</div><div style="width:180px">12</div><div style="width:180px">8%</div></div>
      <div class="row"><div style="width:180px">2018-04-05</div><div style="width:180px">2018-04-07</div><div style="width:180px">19</div><div style="width:180px">6%</div></div>
    </div>
    <div class="gutter" style="left:680px"></div>
    <div class="scroll" style="left:691px"><i></i></div>
  </section>
</div>
</body>
</html>
```